Design my site www.brieflyledger.com

So here is what I am thinking in terms of design:

https://plenvo.com

https://www.skyluxair.com

http://kalvex.com/harbor-plaza-tower/

I want the theme to be white and blue (royal blue). I attached a paint picture of what I would like the site to look like in terms of placing the text. Generally, what I like about the sites above is that they are simple, you can navigate easily and have some kind of idea of what's going on by looking at the center (picture and motto). Let's establish a clear understanding of how the functional part of the site would look like. Please see the picture attached.

I want to keep it simple: On top would be the Name 'BRIEFLY ledger", somewhere to the right on top on the page would be 'Sign in" button.

In the center would be a picture (maybe a video) with the Motto (on top of it all in capital) OBSERVE NAVIGATE DECIDE and below would be the "sign up now"

Below the picture (like on kalvex.com site) or to the left on top of the page would be "About Us', "Press" "Contact Us' buttons.

Then once the user gets to his page his got 3 tabs " Press Headlines", "Events", " Briefings".

we would keep the same format I only have on the site, but separate for every Tab.

I do not want the user to get distracted. I also want him to be able to access the page though mobile phone and be able to get automatic updates just like Zorvan Pings without having to sign in daily.

The landing page must be minimalist yet with business/corporate feel where users can navigate easily and a "what you see is what you get" approach. You want an image or video (personally I prefer the video.. it does capture the users attention instantly, as long as it is an interesting video), with your taglines in it.

Sections available to public: About Us, Contact Us, Landing Page with Signup Option

Private: Public Sections + User Account Page, Tabs for (Events, Press Headlines, Briefings)

Target Market(s)

PR/media monitoring/diplomatic community

Coding

Coded - Design and coding required

Number of Pages Required

1 page

Font styles to use
Serif
Sans Serif

Colors
0255a3
ec1f27

Requirements
Must have
• a simple landing page, that is user friendly.
Nice to have
• a video with the explanation of how to navigate the site
Should not have
• too many colors, graphs etc.

```html
<!DOCTYPE html>
<html lang="en">
<head>
<meta charset="utf-8">
<title>BRIEFLY ledger</title>
<link rel="stylesheet" href="https://fonts.googleapis.com/css2?family=Open+Sans:wght@400;600;700&display=swap">
<style>
  :root {
    --blue: #2b8fc1;
    --ink: #333;
    --ink-soft: #555;
    --panel: #f5f5f5;
    --rule: #dcdcdc;
    --white: #fff;
    --hero-top: #3a4a63;
    --hero-bottom: #1b2433;
  }
  * { box-sizing: border-box; margin: 0; padding: 0; }
  html, body { width: 1200px; height: 896px; overflow: hidden; }
  body { font-family: "Open Sans", Arial, sans-serif; color: var(--ink); background: var(--white); position: relative; }

  .hero {
    position: absolute; left: 0; top: 0; width: 1200px; height: 258px;
    background: linear-gradient(180deg, #4a5670 0%, var(--hero-top) 20%, #2c374b 55%, var(--hero-bottom) 100%);
    border-top: 1px solid var(--blue);
  }
  .brand {
    position: absolute; left: 113px; top: 42px; height: 52px;
    display: flex; align-items: center;
    font-weight: 600; font-size: 30px; color: var(--white); letter-spacing: 0.3px;
  }
  .sign-in {
    position: absolute; left: 982px; top: 51px; width: 83px; height: 33px;
    background: var(--blue); color: var(--white); border: 1px solid #7cc3e6; border-radius: 3px;
    font-weight: 700; font-size: 13.5px; display: flex; align-items: center; justify-content: center;
  }
  .menu-toggle { position: absolute; left: 1079px; top: 58px; }

  .tabs { position: absolute; left: 99px; top: 296px; width: 1002px; height: 42px; border-bottom: 1px solid var(--blue); }
  .tab { position: absolute; top: 0; height: 42px; display: flex; align-items: center; justify-content: center;
    font-size: 15.5px; font-weight: 600; color: #3a3a3a; letter-spacing: 0.2px; }
  .tab--press { left: 32px; }
  .tab--events { left: 212px; width: 206px; background: var(--blue); color: var(--white); }
  .tab--briefings { left: 469px; }

  .panel { position: absolute; left: 99px; top: 338px; width: 1002px; height: 381px;
    background: var(--panel); border: 1px solid var(--rule); border-top: none; }

  .story { position: absolute; top: 41px; }
  .story__media { height: 150px; }
  .story--one .story__media { background: linear-gradient(135deg, #b7bcc0, #7d858c 60%, #c8b98a); }
  .story--two .story__media { background: linear-gradient(135deg, #3a4c52, #b0652e 50%, #2b3a3e); }
  .story--three .story__media { background: linear-gradient(135deg, #1f2531, #4b5a78 60%, #2f3f9a); border-top: 1px solid #d3323a; }
  .story__title { margin-top: 17px; font-size: 15px; font-weight: 400; color: var(--blue); letter-spacing: 0.3px; }
  .story__meta { margin-top: 12px; font-size: 12.5px; font-weight: 400; color: #444; display: flex; align-items: center; gap: 5px; letter-spacing: 0.2px; }
  .story__text { margin-top: 10px; font-size: 11.3px; line-height: 20.5px; color: var(--ink-soft); }
  .story__rule { margin-top: 9px; border-top: 1px dashed #d8d8d8; width: 292px; }

  .story--one { left: 28px; width: 298px; }
  .story--two { left: 356px; width: 293px; }
  .story--three { left: 677px; width: 293px; }

  .footer { position: absolute; left: 0; top: 785px; width: 1200px; height: 111px;
    background: var(--panel); border-top: 1px solid #e3e3e3; }
  .footer__nav { position: absolute; left: 99px; top: 37px; font-size: 12.8px; color: var(--blue); display: flex; gap: 13px; }
  .footer__nav .sep { color: #333; }
  .footer__legal { position: absolute; left: 98px; top: 64px; font-size: 12.8px; color: #333; }
  .social { position: absolute; left: 927px; top: 36px; display: flex; gap: 9.5px; }
  .social span { width: 27px; height: 27px; border-radius: 50%; background: var(--blue); display: block; }
</style>
</head>
<body>
  <header class="hero" role="img" aria-label="Night skyline of a dense city with tall office towers">
    <div class="brand">BRIEFLY LEDGER</div>
    <div class="sign-in">SIGN IN</div>
    <svg class="menu-toggle" width="22" height="20" viewBox="0 0 22 20" aria-label="Menu">
      <rect x="0" y="0" width="22" height="4" fill="#fff"/>
      <rect x="0" y="8" width="22" height="4" fill="#fff"/>
      <rect x="0" y="16" width="22" height="4" fill="#fff"/>
    </svg>
  </header>

  <nav class="tabs">
    <div class="tab tab--press">PRESS HEADLINES</div>
    <div class="tab tab--events">EVENTS</div>
    <div class="tab tab--briefings">BRIEFINGS</div>
  </nav>

  <section class="panel">
    <article class="story story--one">
      <div class="story__media" role="img" aria-label="Commuters waiting at a city street crossing"></div>
      <h3 class="story__title">Nemo enim ipsam voluptatem</h3>
      <p class="story__meta"><svg width="11" height="11" viewBox="0 0 12 12"><circle cx="6" cy="6" r="4.8" fill="none" stroke="#333" stroke-width="1.8"/><path d="M6 3.3V6h2" stroke="#333" stroke-width="1.4" fill="none"/></svg>3 minutes ago, 0 comments</p>
      <p class="story__text">Lorem ipsum dolor sit amet, consectetur adipiscing elit, sed do eiusmod tempor ncididunt ut labore</p>
      <div class="story__rule"></div>
    </article>
    <article class="story story--two">
      <div class="story__media" role="img" aria-label="Operator at a control desk facing glowing industrial machinery"></div>
      <h3 class="story__title">Nemo enim ipsam voluptatem</h3>
      <p class="story__meta"><svg width="11" height="11" viewBox="0 0 12 12"><circle cx="6" cy="6" r="4.8" fill="none" stroke="#333" stroke-width="1.8"/><path d="M6 3.3V6h2" stroke="#333" stroke-width="1.4" fill="none"/></svg>3 minutes ago, 0 comments</p>
      <p class="story__text">Lorem ipsum dolor sit amet, consectetur adipiscing elit, sed do eiusmod tempor ncididunt ut labore</p>
      <div class="story__rule"></div>
    </article>
    <article class="story story--three">
      <div class="story__media" role="img" aria-label="Speaker at a podium during a diplomatic conference with flags"></div>
      <h3 class="story__title">Nemo enim ipsam voluptatem</h3>
      <p class="story__meta"><svg width="11" height="11" viewBox="0 0 12 12"><circle cx="6" cy="6" r="4.8" fill="none" stroke="#333" stroke-width="1.8"/><path d="M6 3.3V6h2" stroke="#333" stroke-width="1.4" fill="none"/></svg>3 minutes ago, 0 comments</p>
      <p class="story__text">Lorem ipsum dolor sit amet, consectetur adipiscing elit, sed do eiusmod tempor ncididunt ut labore</p>
      <div class="story__rule"></div>
    </article>
  </section>

  <footer class="footer">
    <div class="footer__nav"><span>ABOUT US</span><span class="sep">/</span><span>PRESS</span><span class="sep">/</span><span>CONTACT US</span></div>
    <div class="footer__legal">2016 © Copyrights BRIEFLY ledger.All Rights Reserved</div>
    <div class="social" aria-label="Social links"><span></span><span></span><span></span><span></span><span></span></div>
  </footer>
</body>
</html>
```